Voltride Cycles Company

I need a Voltride Cycles site for pre-orders, 3-4 models, multiple colors per order. The bikes are electric bikes, company logo color scheme has red. Maybe a countdown to a date when pre-order will close. I also want to incorporate a deposit style system for the pre-order with the balance due on shipping.

```html
<!DOCTYPE html>
<html lang="en">
<head>
<meta charset="utf-8">
<title>Voltride Cycles – Electric Bike Pre-Orders</title>
<link href="https://fonts.googleapis.com/css2?family=Poppins:wght@400;500;600;700&display=swap" rel="stylesheet">
<style>
:root{
  --red:#8a0b0e;
  --red-dark:#6e0709;
  --ink:#1c1c1c;
  --muted:#555;
  --line:#d9d9d9;
  --hero-bg:#f1f1f1;
  --white:#fff;
  --blue-note:#1b63b5;
}
*{box-sizing:border-box;margin:0;padding:0}
html,body{width:1200px;height:4577px;overflow:hidden;background:var(--white)}
body{font-family:'Poppins',sans-serif;color:var(--ink)}
.page{position:relative;width:1200px;height:4577px;overflow:hidden}
.abs{position:absolute}
.ph{position:absolute}

/* top bar */
.topbar{left:0;top:0;width:1200px;height:34px;background:var(--red);color:var(--white);font-size:13px;font-weight:500}
.topbar .note{position:absolute;left:0;right:0;top:8px;text-align:center}
.topbar .social{position:absolute;left:80px;top:9px;display:flex;gap:8px}
.topbar .social span{width:16px;height:16px;border:1.5px solid var(--white);border-radius:50%}
.topbar .lang{position:absolute;right:68px;top:8px}

/* header */
.brand{font-weight:600;color:var(--red)}
.header-logo{left:82px;top:64px;font-size:26px}
.search{left:540px;top:64px;width:335px;height:36px;border:2px solid var(--red);border-radius:18px;font-size:12px;color:var(--muted);display:flex;align-items:center;gap:10px;padding-left:4px}
.search .icon{width:28px;height:28px;border-radius:50%;background:var(--red);display:flex;align-items:center;justify-content:center}
.pill{height:36px;border-radius:18px;display:flex;align-items:center;gap:8px;padding-left:4px;font-size:13px;font-weight:600}
.pill .icon{width:28px;height:28px;border-radius:50%;background:var(--red);display:flex;align-items:center;justify-content:center}
.account{left:889px;top:64px;width:123px;background:var(--red);color:var(--white)}
.account .icon{background:var(--white)}
.cart{left:1026px;top:64px;width:105px;border:2px solid var(--red);color:var(--ink)}
.header-rule{left:0;top:128px;width:1200px;height:1px;background:var(--line)}
.nav{top:151px;font-size:14px}
.service{top:144px;font-size:12px;color:var(--red);line-height:18px}

/* hero */
.hero{left:0;top:196px;width:1200px;height:640px;background:linear-gradient(120deg,#f7f7f7 0%,#ececec 55%,#f6f6f6 100%)}
.hero-title{left:82px;top:330px;font-size:39px;font-weight:700;line-height:48px;letter-spacing:.5px}
.btn{display:flex;align-items:center;justify-content:center;border-radius:20px;font-weight:600}
.btn-red{background:var(--red);color:var(--white)}
.btn-outline{border:2px solid var(--ink);color:var(--ink);background:var(--white)}
.preorder{left:82px;top:500px;width:133px;height:36px;font-size:16px}
.countdown{left:82px;top:567px;width:396px;height:164px;background:var(--red);border-radius:12px;color:var(--white);padding:22px 26px}
.countdown h3{font-size:26px;font-weight:600}
.countdown .digits{display:flex;gap:10px;margin-top:4px;font-size:46px;font-weight:600;line-height:56px}
.countdown .labels{display:flex;font-size:15px}
.countdown .labels span{width:98px}
.hero-bike{left:658px;top:293px;width:444px;height:391px;background:radial-gradient(ellipse at center,#4a4a4a 0%,#2b2b2b 45%,rgba(241,241,241,0) 72%)}
.dots{display:flex;align-items:center;gap:10px;color:var(--red);font-size:12px}
.dots .on{width:28px;height:4px;background:var(--red);border-radius:2px}
.dots .off{width:6px;height:6px;background:#bbb;border-radius:50%}

/* section headings */
.sec-title{font-size:31px;font-weight:600;letter-spacing:.5px}
.sec-title em{font-style:normal;color:var(--red)}
.view-all{left:1004px;top:957px;font-size:13px;font-weight:600;border-bottom:1.5px solid var(--ink)}

/* product cards */
.card{top:1008px;width:242px;height:381px;background:var(--white);border:1px solid #ccc;border-radius:8px;box-shadow:0 3px 6px rgba(0,0,0,.18)}
.badge{position:absolute;right:16px;top:14px;height:22px;padding:0 10px;font-size:11px;font-weight:600;color:var(--white);border-radius:3px;display:flex;align-items:center}
.badge.new{background:#5ba35b}.badge.sale{background:var(--red)}.badge.sold{background:#888}
.card .pic{left:20px;top:45px;width:202px;height:140px;border-radius:6px}
.card .price{position:absolute;left:18px;top:187px;font-size:16px;color:#333}
.card .name{position:absolute;left:18px;top:218px;font-size:18px;font-weight:500}
.stars{font-size:14px;letter-spacing:2px}
.stars small{font-size:12px;color:#666;letter-spacing:0;margin-left:6px}
.card .stars{position:absolute;left:18px;top:248px}
.swatches{display:flex;gap:10px}
.swatches i{width:20px;height:20px;border-radius:50%;display:block}
.card .swatches{position:absolute;left:18px;top:280px}
.card .btn{position:absolute;left:18px;top:320px;width:198px;height:34px;font-size:12px}

/* mountain banner */
.mountain{left:0;top:1533px;width:1200px;height:551px;background:linear-gradient(180deg,#8fb6d8 0%,#c9d8e0 35%,#8a9a8a 55%,#4f8a2c 75%,#3a6d1f 100%)}
.mini{top:1632px;width:254px;height:352px;background:rgba(255,255,255,.93);border-radius:6px}
.mini .pic{left:20px;top:36px;width:214px;height:120px;border-radius:6px}
.mini .from{position:absolute;left:28px;top:168px;font-size:16px;color:#444}
.mini .name{position:absolute;left:28px;top:196px;font-size:19px;font-weight:500}
.mini .stars{position:absolute;left:28px;top:228px;font-size:17px}
.mini .btn{position:absolute;left:28px;top:288px;width:198px;height:34px;font-size:12px}
.mini .heart{position:absolute;right:14px;top:12px}
.mini-dots{left:52px;top:2010px}
.mini-dots .on{background:var(--white)}.mini-dots .off{background:var(--white)}

/* features */
.features-title{left:0;width:1200px;top:2160px;text-align:center}
.feat-bike{left:347px;top:2365px;width:498px;height:311px;background:radial-gradient(ellipse at center,#b8272b 0%,#7a3436 30%,#3b3b3b 50%,rgba(255,255,255,0) 72%)}
.feat-dot{width:74px;height:74px;border-radius:50%;border:2.5px solid var(--red);background:linear-gradient(135deg,#f4f4f4,#bdbdbd)}
.feat-label{font-size:18px;font-weight:500}

/* promo banner */
.promo{left:0;top:2757px;width:1200px;height:438px;background:linear-gradient(100deg,#3a3a36 0%,#1f1f1d 40%,#4c4a44 70%,#9a9789 100%)}
.promo-kicker{left:681px;top:2856px;font-size:14px;font-weight:600;color:var(--white)}
.promo-title{left:681px;top:2886px;font-size:32px;font-weight:700;color:var(--white);letter-spacing:1.5px}
.promo-copy{left:678px;top:2942px;width:460px;font-size:14px;line-height:25px;color:var(--white)}
.promo-btn{left:681px;top:3058px;width:130px;height:34px;font-size:13px}

/* product detail */
.detail-pic{left:103px;top:3310px;width:457px;height:495px;background:linear-gradient(180deg,#8ea9c4 0%,#6c8fb0 30%,#5a5650 45%,#8d8478 75%,#6f675d 100%)}
.zoom{left:503px;top:3340px}
.old{text-decoration:line-through;color:#777}
.d-price{left:613px;top:3386px;font-size:19px;font-weight:500}
.d-title{left:613px;top:3421px;font-size:30px;font-weight:500}
.d-copy{left:613px;top:3467px;width:470px;font-size:15px;line-height:24px;color:#444}
.d-sale{left:613px;top:3584px;font-size:27px;font-weight:600;color:var(--blue-note)}
.d-save{left:736px;top:3614px;font-size:11px;font-weight:600;color:var(--blue-note)}
.d-swatches{left:617px;top:3650px}
.d-swatches i{width:24px;height:24px}
.d-rule{left:613px;top:3708px;width:484px;height:1px;background:var(--line)}
.qty{top:3740px;width:48px;height:48px;border:2.5px solid var(--ink);border-radius:50%;display:flex;align-items:center;justify-content:center;font-size:26px;font-weight:500}
.qty-num{left:690px;top:3746px;font-size:24px}
.add-cart{left:809px;top:3746px;width:133px;height:36px;font-size:13px}
.buy-now{left:955px;top:3746px;width:125px;height:36px;font-size:13px}

/* testimonial */
.testimonial{left:82px;top:3897px;width:1049px;height:317px;background:var(--red)}
.avatar{left:473px;top:3947px;width:96px;height:96px;border-radius:50%;background:linear-gradient(180deg,#cfcfcf,#9b9b9b);border:3px solid var(--white)}
.t-name{left:583px;top:3970px;font-size:20px;font-weight:600;color:var(--white)}
.t-role{left:583px;top:3998px;font-size:13px;font-weight:600;color:var(--white)}
.t-copy{left:150px;top:4062px;width:913px;text-align:center;font-size:15px;line-height:25px;color:var(--white)}

/* footer */
.foot-logo{left:82px;top:4290px;font-size:30px}
.foot-head{top:4292px;font-size:24px;font-weight:500;color:var(--red)}
.foot-list{list-style:none;font-size:14px;line-height:28px}
.foot-about{left:784px;top:4336px;width:347px;font-size:14px;line-height:25px;text-align:justify}
.foot-rule{left:103px;top:4521px;width:1000px;height:1px;background:var(--line)}
.copyright{left:0;width:1200px;top:4542px;text-align:center;font-size:13px}
.pay{left:871px;top:4542px;display:flex;gap:4px}
.pay i{width:32px;height:20px;border-radius:3px;display:block}
</style>
</head>
<body>
<div class="page">

  <!-- top bar -->
  <div class="abs topbar">
    <div class="social"><span></span><span></span><span></span></div>
    <div class="note">Free Shipping On Orders Above $50</div>
    <div class="lang">EN &#8964;</div>
  </div>

  <!-- header -->
  <div class="abs brand header-logo">Voltride Cycles</div>
  <div class="abs search">
    <span class="icon"><svg width="14" height="14" viewBox="0 0 14 14"><circle cx="6" cy="6" r="4.5" fill="none" stroke="#fff" stroke-width="1.8"/><line x1="9.3" y1="9.3" x2="13" y2="13" stroke="#fff" stroke-width="1.8"/></svg></span>
    Search For...
  </div>
  <div class="abs pill account">
    <span class="icon"><svg width="14" height="14" viewBox="0 0 14 14"><circle cx="7" cy="4.5" r="3" fill="#8a0b0e"/><path d="M1.5 13c0-3.2 2.5-5 5.5-5s5.5 1.8 5.5 5z" fill="#8a0b0e"/></svg></span>
    Account
  </div>
  <div class="abs pill cart">
    <span class="icon"><svg width="14" height="14" viewBox="0 0 14 14"><rect x="2.5" y="5" width="9" height="8" rx="1" fill="#fff"/><path d="M4.5 5V4a2.5 2.5 0 0 1 5 0v1" fill="none" stroke="#fff" stroke-width="1.5"/></svg></span>
    $0.00
  </div>

  <div class="abs nav" style="left:80px">Electric Bikes</div>
  <div class="abs nav" style="left:210px">About Us</div>
  <div class="abs nav" style="left:316px">Our stores</div>
  <div class="abs nav" style="left:432px">Tesimonials</div>
  <div class="abs nav" style="left:560px">Blog</div>
  <div class="abs nav" style="left:633px">FAQ</div>

  <svg class="abs" style="left:853px;top:148px" width="28" height="28" viewBox="0 0 28 28"><path d="M3 4h22l2 7H1z" fill="#8a0b0e"/><rect x="4" y="12" width="20" height="14" fill="none" stroke="#8a0b0e" stroke-width="2.5"/><rect x="11" y="17" width="6" height="9" fill="#8a0b0e"/></svg>
  <div class="abs service" style="left:889px">Picking up?<br>Select store</div>
  <svg class="abs" style="left:990px;top:150px" width="40" height="26" viewBox="0 0 40 26"><rect x="1" y="3" width="24" height="15" fill="#8a0b0e"/><path d="M25 8h8l5 6v4H25z" fill="#8a0b0e"/><circle cx="9" cy="21" r="4" fill="#8a0b0e" stroke="#fff" stroke-width="1.5"/><circle cx="31" cy="21" r="4" fill="#8a0b0e" stroke="#fff" stroke-width="1.5"/></svg>
  <div class="abs service" style="left:1038px">Need delivery?<br>See estimates</div>
  <div class="abs header-rule"></div>

  <!-- hero -->
  <section class="abs hero"></section>
  <div class="ph hero-bike" role="img" aria-label="Black fat-tyre electric bike with red rim accents, side view"></div>
  <h1 class="abs hero-title">RESERVE THE<br>PRODUCT WITH INTIAL<br>PAYMENT OF 10%</h1>
  <div class="abs btn btn-red preorder">Pre - Order</div>
  <div class="abs countdown">
    <h3>Hurry Up Sales In!</h3>
    <div class="digits"><span>01</span>:<span>06</span>:<span>30</span>:<span>30</span></div>
    <div class="labels"><span>Days</span><span>Hrs</span><span>Mins</span><span>Secs</span></div>
  </div>
  <div class="abs dots" style="left:562px;top:860px">&lsaquo;<span class="on"></span><span class="off"></span>&rsaquo;</div>

  <!-- best sellers -->
  <h2 class="abs sec-title" style="left:82px;top:947px">BEST <em>SELLERS</em></h2>
  <div class="abs view-all">View All Products</div>

  <div class="abs card" style="left:82px">
    <span class="badge new">NEW</span>
    <div class="ph pic" role="img" aria-label="Black step-through electric city bike" style="background:radial-gradient(ellipse at center,#3a3a3a 0%,#777 35%,#fff 70%)"></div>
    <div class="price">$160.00</div><div class="name">Bicycle 1</div>
    <div class="stars">★★★★★<small>(4)</small></div>
    <div class="swatches"><i style="background:#333"></i><i style="background:#8a0b0e"></i><i style="background:#ddd"></i><i style="background:#666"></i></div>
    <div class="btn btn-outline">BUY NOW</div>
  </div>
  <div class="abs card" style="left:350px">
    <span class="badge sale">10%</span>
    <div class="ph pic" role="img" aria-label="Black electric mountain bike with green tyres" style="background:radial-gradient(ellipse at center,#2d2d2d 0%,#6fa04a 38%,#fff 70%)"></div>
    <div class="price">$260.00</div><div class="name">ebike 2</div>
    <div class="stars">★★★★★<small>(4)</small></div>
    <div class="swatches"><i style="background:#333"></i><i style="background:#8a0b0e"></i><i style="background:#ddd"></i><i style="background:#7ed07e"></i></div>
    <div class="btn btn-red">BUY NOW</div>
  </div>
  <div class="abs card" style="left:619px">
    <span class="badge sold">UN SOLD</span>
    <div class="ph pic" role="img" aria-label="Grey electric trekking bike" style="background:radial-gradient(ellipse at center,#444 0%,#888 35%,#fff 70%)"></div>
    <div class="price">$560.00</div><div class="name">ebike 3</div>
    <div class="stars">★★★★★<small>(4)</small></div>
    <div class="swatches"><i style="background:#333"></i><i style="background:#8a0b0e"></i><i style="background:#ddd"></i><i style="background:#666"></i></div>
    <div class="btn btn-outline">BUY NOW</div>
  </div>
  <div class="abs card" style="left:887px">
    <span class="badge new">NEW</span>
    <div class="ph pic" role="img" aria-label="Red electric city bike" style="background:radial-gradient(ellipse at center,#b3262a 0%,#999 35%,#fff 70%)"></div>
    <div class="price">$80.00</div><div class="name">ebike 3</div>
    <div class="stars">★★★★★<small>(4)</small></div>
    <div class="swatches"><i style="background:#333"></i><i style="background:#8a0b0e"></i><i style="background:#ddd"></i><i style="background:#666"></i></div>
    <div class="btn btn-outline">BUY NOW</div>
  </div>
  <div class="abs dots" style="left:562px;top:1449px">&lsaquo;<span class="on"></span><span class="off"></span>&rsaquo;</div>

  <!-- mountain banner -->
  <div class="ph mountain" role="img" aria-label="Electric mountain bike standing on a grassy slope with mountains and blue sky behind"></div>
  <div class="abs mini" style="left:46px">
    <svg class="heart" width="18" height="16" viewBox="0 0 18 16"><path d="M9 15S1 10 1 5a4 4 0 0 1 8-1 4 4 0 0 1 8 1c0 5-8 10-8 10z" fill="none" stroke="#333" stroke-width="1.3"/></svg>
    <div class="ph pic" role="img" aria-label="Yellow electric mountain bike" style="background:radial-gradient(ellipse at center,#e2c52a 0%,#555 35%,rgba(255,255,255,0) 70%)"></div>
    <div class="from">From $60.00</div><div class="name">ebike</div>
    <div class="stars">☆☆☆☆☆</div>
    <div class="btn btn-outline">BUY NOW</div>
  </div>
  <div class="abs mini" style="left:318px">
    <svg class="heart" width="18" height="16" viewBox="0 0 18 16"><path d="M9 15S1 10 1 5a4 4 0 0 1 8-1 4 4 0 0 1 8 1c0 5-8 10-8 10z" fill="none" stroke="#333" stroke-width="1.3"/></svg>
    <div class="ph pic" role="img" aria-label="Blue electric mountain bike" style="background:radial-gradient(ellipse at center,#2b4fa8 0%,#555 35%,rgba(255,255,255,0) 70%)"></div>
    <div class="from">From $60.00</div><div class="name">ebike</div>
    <div class="stars">☆☆☆☆☆</div>
    <div class="btn btn-red">BUY NOW</div>
  </div>
  <div class="abs dots mini-dots" style="color:#fff">&lsaquo;<span class="on"></span><span class="off"></span><span class="off"></span>&rsaquo;</div>

  <!-- features -->
  <h2 class="abs sec-title features-title">E BIKE <em>FEATURES</em></h2>
  <div class="ph feat-bike" role="img" aria-label="Red step-through electric bike with callouts to its components"></div>
  <div class="ph feat-dot" role="img" aria-label="Saddle close-up" style="left:491px;top:2248px"></div>
  <div class="abs feat-label" style="left:579px;top:2248px">Lorem Ipsum</div>
  <div class="ph feat-dot" role="img" aria-label="Rear rack close-up" style="left:237px;top:2313px"></div>
  <div class="abs feat-label" style="left:323px;top:2312px">Lorem Ipsum</div>
  <div class="ph feat-dot" role="img" aria-label="Front fork close-up" style="left:811px;top:2288px"></div>
  <div class="abs feat-label" style="left:899px;top:2289px">Lorem Ipsum</div>
  <div class="ph feat-dot" role="img" aria-label="Disc brake close-up" style="left:882px;top:2425px"></div>
  <div class="abs feat-label" style="left:971px;top:2425px">Lorem Ipsum</div>
  <div class="ph feat-dot" role="img" aria-label="Fender close-up" style="left:237px;top:2612px"></div>
  <div class="abs feat-label" style="left:311px;top:2680px">Lorem Ipsum</div>
  <div class="ph feat-dot" role="img" aria-label="Chainring close-up" style="left:827px;top:2624px"></div>
  <div class="abs feat-label" style="left:915px;top:2625px">Lorem Ipsum</div>

  <!-- promo banner -->
  <div class="ph promo" role="img" aria-label="Rider standing beside a black electric bike in front of a dark slatted wall"></div>
  <div class="abs promo-kicker">UP TO 50% DISCOUNT</div>
  <h2 class="abs promo-title">ELECTRIC BIKES</h2>
  <p class="abs promo-copy">Lorem ipsum dolor sit amet, consectetur adipiscing elit, sed do eiusmod tempor incididunt ut labore et dolore magna aliqua. Ut enim ad minim veniam, quis nostrud exercitation ullamco laboris nisi ut aliquip ex ea commodo consequat</p>
  <div class="abs btn btn-red promo-btn">BUY NOW</div>

  <!-- product detail -->
  <div class="ph detail-pic" role="img" aria-label="Black fat-tyre electric bike parked on a pebble beach by the sea"></div>
  <svg class="abs zoom" width="26" height="26" viewBox="0 0 26 26"><circle cx="11" cy="11" r="8" fill="none" stroke="#222" stroke-width="1.8"/><line x1="17" y1="17" x2="24" y2="24" stroke="#222" stroke-width="2"/><line x1="7" y1="11" x2="15" y2="11" stroke="#222" stroke-width="1.6"/><line x1="11" y1="7" x2="11" y2="15" stroke="#222" stroke-width="1.6"/></svg>
  <div class="abs d-price">$60.00 &nbsp;<span class="old">$90.00</span></div>
  <h2 class="abs d-title">Electric Bikes</h2>
  <p class="abs d-copy">Lorem ipsum dolor sit amet, consectetur adipiscing elit, sed do eiusmod tempor incididunt ut labore et dolore magna aliqua. Ut enim ad minim veniam, quis nostrud exercitation ullamco laboris nisi ut aliquip ex ea commodo consequat.</p>
  <div class="abs d-sale">$560.00 <span class="old" style="font-size:20px;font-weight:400;margin-left:10px">$790.00</span></div>
  <div class="abs d-save">YOU SAVE $30</div>
  <div class="abs swatches d-swatches"><i style="background:#f2c318"></i><i style="background:#e8792c;outline:2px solid #333;outline-offset:1px"></i><i style="background:#6c6650"></i><i style="background:#111"></i></div>
  <div class="abs d-rule"></div>
  <div class="abs qty" style="left:624px">&minus;</div>
  <div class="abs qty-num">1</div>
  <div class="abs qty" style="left:727px">+</div>
  <div class="abs btn btn-red add-cart">ADD TO CART</div>
  <div class="abs btn btn-outline buy-now">BUY NOW</div>

  <!-- testimonial -->
  <section class="abs testimonial"></section>
  <div class="ph avatar" role="img" aria-label="Customer portrait"></div>
  <div class="abs t-name">Daniel Reyes</div>
  <div class="abs t-role">Customer</div>
  <p class="abs t-copy">Lorem ipsum dolor sit amet, consectetur adipiscing elit, sed do eiusmod tempor incididunt ut labore et dolore magna aliqua. Ut enim ad minim veniam, quis nostrud exercitation ullamco laboris nisi ut aliquip ex ea commodo consequat. Duis aute irure dolor in reprehenderit in voluptate velit esse cillum dolore eu fugiat nulla pariatur. Excepteur sint occaecat cupidatat non proident, sunt in culpa qui officia deserunt mollit anim id est laborum.</p>

  <!-- footer -->
  <div class="abs brand foot-logo">Voltride Cycles</div>
  <div class="abs foot-head" style="left:428px">Quick Link</div>
  <ul class="abs foot-list" style="left:428px;top:4336px">
    <li>Electric Bikes</li><li>About Us</li><li>Our stores</li><li>Tesimonials</li><li>Blog</li><li>FAQ</li>
  </ul>
  <div class="abs foot-head" style="left:610px">Help Links</div>
  <ul class="abs foot-list" style="left:610px;top:4336px;line-height:30px">
    <li>Search</li><li>About Us</li><li>Delivery</li><li>Our stores</li>
  </ul>
  <div class="abs foot-head" style="left:784px">About Us</div>
  <p class="abs foot-about">Lorem ipsum dolor sit amet, consectetur adipiscing elit, sed do eiusmod tempor incididunt ut labore et dolore magna aliqua. Ut enim ad minim veniam, quis nostrud exercitation ullamco laboris nisi ut aliquip ex ea commodo consequat.</p>
  <div class="abs foot-rule"></div>
  <div class="abs copyright">Copyright © 2023 Voltride Cycles | All Rights Reserved</div>
  <div class="abs pay"><i style="background:#333"></i><i style="background:#dfe6ef"></i><i style="background:#e9ecf4"></i><i style="background:#eee"></i><i style="background:#2c6fb5"></i><i style="background:#e8492a"></i></div>

</div>
</body>
</html>
```